TREVAL BUILDWORKS, LLC Webpage portfolio

I want to create a Website that allows my potential clients to browse my Skilled work via before and after photos. I want the website to enhance the work that I provide and potentially drive new business, or at least solidify my work.
I also do 3D CAD and Modeling of New Spaces and it would be nice to show some of that work from pencil design to 3D modeling, which I feel may help give me more clients.

The website needs to show a solid carpenter/company with the skills to get any project completed.

Types of Jobs - Custom Carpentry & Finishes, Kitchens, Baths, Basements, Decks, Porches, Whole House Renovation - Skilled Craftsmanship (Hardwood Flooring, Floor and Wall Tile) and much more...

Target Market(s)

Residential Home Renovation, Kitchen and Bath Renovation, Home Improvement

Industry/Entity Type

Residential Construction

Number of Pages Required

5+ page

Font styles to use
Sans Serif
Script

Requirements
Must have
• Similar to Plinvo.com, except for Treval Buildworks.
• Must be inviting.
• My Services Offered
• A way to reach me or contact me for estimates with some sort of Screening Questionare.
Nice to have
• Inviting Colors
Should not have
• Not sure at this time

```html
<!DOCTYPE html>
<html lang="en">
<head>
<meta charset="utf-8">
<title>Treval Buildworks – Request an Estimate</title>
<link href="https://fonts.googleapis.com/css2?family=Quicksand:wght@300;400;500;600&display=swap" rel="stylesheet">
<style>
  :root {
    --page-bg: #1b1b1b;
    --panel-bg: #0a0a0a;
    --text: #e6e6e6;
    --text-soft: #c9c9c9;
    --field-border: #3a3a3a;
    --field-bg: #0d0d0d;
    --control: #4a4a4a;
    --button-bg: #2a2a2a;
  }
  * { box-sizing: border-box; margin: 0; padding: 0; }
  html, body { width: 1200px; height: 2550px; overflow: hidden; }
  body {
    position: relative;
    background: var(--page-bg);
    color: var(--text);
    font-family: "Quicksand", sans-serif;
  }
  .content-panel {
    position: absolute; left: 139px; top: 150px; width: 1012px; height: 2400px;
    background: var(--panel-bg);
  }
  .brand {
    position: absolute; left: 51px; top: 44px;
    display: flex; align-items: center; gap: 8px;
    font-size: 15px; font-weight: 600; color: var(--text);
  }
  .brand-mark { width: 14px; height: 14px; background: var(--text-soft); }
  .top-social { position: absolute; left: 888px; top: 21px; display: flex; gap: 14px; }
  .social-dot { width: 12px; height: 12px; border-radius: 50%; background: var(--text); }
  .phone { position: absolute; left: 1047px; top: 19px; font-size: 11px; color: var(--text); }
  .main-nav { position: absolute; right: 49px; top: 76px; display: flex; gap: 18px; font-size: 14px; font-weight: 500; }
  .page-title {
    position: absolute; left: 51px; top: 146px;
    font-size: 37px; font-weight: 300; line-height: 44px; letter-spacing: 1px;
  }
  .section-label {
    position: absolute; left: 51px; width: 170px;
    font-size: 10px; font-weight: 500; line-height: 13px; text-transform: uppercase; color: var(--text-soft);
  }
  .field-label { position: absolute; left: 300px; font-size: 10px; font-weight: 500; text-transform: uppercase; }
  .text-input {
    position: absolute; left: 300px; width: 802px; height: 31px;
    border: 1px solid var(--field-border); background: var(--field-bg);
  }
  .question { position: absolute; left: 300px; font-size: 15px; font-weight: 500; }
  .option {
    position: absolute; display: flex; align-items: flex-start; gap: 15px;
    font-size: 10px; font-weight: 500; line-height: 13px; color: var(--text-soft);
  }
  .checkbox { width: 15px; height: 15px; border: 1px solid var(--control); flex: none; margin-top: -2px; }
  .radio { width: 15px; height: 15px; border-radius: 50%; background: var(--control); flex: none; margin-top: -2px; }
  .scope-area {
    position: absolute; left: 300px; top: 2100px; width: 802px; height: 101px;
    border: 1px solid var(--field-border); background: var(--field-bg);
  }
  .submit-button {
    position: absolute; left: 300px; top: 2450px; width: 150px; height: 50px;
    background: var(--button-bg); color: var(--text);
    font-size: 21px; font-weight: 500; display: flex; align-items: center; justify-content: center;
  }
  .footer-social { position: absolute; left: 498px; top: 2486px; display: flex; gap: 15px; }
</style>
</head>
<body>
  <div class="content-panel"></div>

  <header>
    <div class="brand"><span class="brand-mark"></span>Treval Buildworks</div>
    <div class="top-social"><span class="social-dot"></span><span class="social-dot"></span><span class="social-dot"></span><span class="social-dot"></span></div>
    <div class="phone">+1 (555) 014-2290</div>
    <nav class="main-nav"><span>KITCHENS</span><span>BATHS</span><span>BASEMENTS</span><span>FINISHED CARPENTRY</span><span>DECKS &amp; PORCHES</span></nav>
  </header>

  <h1 class="page-title">REQUEST AN<br>ESTIMATE</h1>

  <!-- Personal details -->
  <div class="section-label" style="top:300px">Personal details and contact information</div>
  <div class="field-label" style="top:298px">Name</div><div class="text-input" style="top:320px"></div>
  <div class="field-label" style="top:378px">Address</div><div class="text-input" style="top:400px"></div>
  <div class="field-label" style="top:458px">City</div><div class="text-input" style="top:479px"></div>
  <div class="field-label" style="top:538px">State</div><div class="text-input" style="top:559px"></div>
  <div class="field-label" style="top:618px">Zip code</div><div class="text-input" style="top:639px"></div>

  <!-- Type of work -->
  <div class="section-label" style="top:746px">Type of work desiring please select options below</div>
  <div class="option" style="left:300px;top:752px"><span class="checkbox"></span>Option 1</div>
  <div class="option" style="left:300px;top:802px"><span class="checkbox"></span>Option 2</div>
  <div class="option" style="left:300px;top:851px"><span class="checkbox"></span>Option 2</div>

  <!-- Professional details -->
  <div class="section-label" style="top:950px">Professional details</div>
  <div class="question" style="top:947px">Are you a veteran ?</div>
  <div class="option" style="left:300px;top:990px"><span class="radio"></span>YES</div>
  <div class="option" style="left:400px;top:990px"><span class="radio"></span>NO</div>
  <div class="question" style="top:1047px">Branch</div>
  <div class="option" style="left:300px;top:1090px"><span class="radio"></span>USN</div>
  <div class="option" style="left:400px;top:1090px"><span class="radio"></span>USA</div>
  <div class="option" style="left:500px;top:1090px"><span class="radio"></span>US Air<br>Force</div>
  <div class="option" style="left:599px;top:1090px"><span class="radio"></span>Current / Discharge</div>

  <!-- Services required -->
  <div class="section-label" style="top:1200px">Types of services required</div>
  <div class="question" style="top:1196px">Do you need Design/Drafting Type drawings done for your project?</div>
  <div class="option" style="left:300px;top:1240px"><span class="radio"></span>YES</div>
  <div class="option" style="left:400px;top:1240px"><span class="radio"></span>NO</div>
  <div class="question" style="top:1296px">What type of project best describes what you are looking to accomplish?</div>
  <div class="option" style="left:300px;top:1351px"><span class="checkbox"></span>New Home Remodel</div>
  <div class="option" style="left:500px;top:1351px"><span class="checkbox"></span>New/Update Kitchen</div>
  <div class="option" style="left:699px;top:1351px"><span class="checkbox"></span>Bath</div>
  <div class="option" style="left:899px;top:1351px"><span class="checkbox"></span>Basement</div>
  <div class="option" style="left:300px;top:1400px"><span class="checkbox"></span>Deck</div>
  <div class="option" style="left:500px;top:1400px"><span class="checkbox"></span>Porch</div>
  <div class="option" style="left:699px;top:1400px"><span class="checkbox"></span>New Flooring</div>
  <div class="option" style="left:899px;top:1400px"><span class="checkbox"></span>New Home Siding</div>

  <!-- Time frames -->
  <div class="section-label" style="top:1500px">Time frames and deadlines</div>
  <div class="question" style="top:1496px">If you approve the Design when are you ready to get started?</div>
  <div class="option" style="left:300px;top:1552px"><span class="checkbox"></span>Immediately</div>
  <div class="option" style="left:500px;top:1552px"><span class="checkbox"></span>1 - 2 Weeks</div>
  <div class="option" style="left:699px;top:1552px"><span class="checkbox"></span>2 - 4 Weeks</div>
  <div class="option" style="left:899px;top:1552px"><span class="checkbox"></span>4 - 6 Weeks</div>
  <div class="option" style="left:300px;top:1601px"><span class="checkbox"></span>3 - 6 Months</div>
  <div class="option" style="left:500px;top:1601px"><span class="checkbox"></span>6 - 9 Months</div>
  <div class="option" style="left:699px;top:1601px"><span class="checkbox"></span>10 Months to Year</div>

  <!-- Payment -->
  <div class="section-label" style="top:1698px">Mode of payment</div>
  <div class="question" style="top:1695px">What mode of payment wil you be using ?</div>
  <div class="option" style="left:300px;top:1750px"><span class="checkbox"></span>Cash / Cheque</div>
  <div class="option" style="left:500px;top:1750px"><span class="checkbox"></span>Corvan Card</div>
  <div class="option" style="left:699px;top:1750px"><span class="checkbox"></span>Meridian Card</div>
  <div class="option" style="left:899px;top:1750px"><span class="checkbox"></span>Axtel Card</div>

  <!-- Other assistance -->
  <div class="section-label" style="top:1850px">Other assistance and services needed</div>
  <div class="question" style="top:1846px">Will you require assistance to move furniture ?</div>
  <div class="option" style="left:801px;top:1851px"><span class="radio"></span>YES</div>
  <div class="option" style="left:903px;top:1851px"><span class="radio"></span>NO</div>
  <div class="question" style="top:1896px">Have you read the 2016 Remodeling Cost guide ?</div>
  <div class="option" style="left:801px;top:1901px"><span class="radio"></span>YES</div>
  <div class="option" style="left:903px;top:1901px"><span class="radio"></span>NO</div>
  <div class="question" style="top:1945px">Are you interested in a Home Flip Venture ?</div>
  <div class="option" style="left:801px;top:1950px"><span class="radio"></span>YES</div>
  <div class="option" style="left:903px;top:1950px"><span class="radio"></span>NO</div>

  <!-- Scope -->
  <div class="section-label" style="top:2050px">Scope of work needed on your home</div>
  <div class="question" style="top:2045px">Tell us something about the scope of work on your home ?</div>
  <div class="scope-area"></div>

  <!-- Style -->
  <div class="section-label" style="top:2300px">What is your style ?</div>
  <div class="question" style="top:2295px">Please select your style ?</div>
  <div class="option" style="left:300px;top:2351px"><span class="radio"></span>Traditional</div>
  <div class="option" style="left:449px;top:2351px"><span class="radio"></span>Classic</div>
  <div class="option" style="left:600px;top:2351px"><span class="radio"></span>Contemporary</div>
  <div class="option" style="left:750px;top:2351px"><span class="radio"></span>Modern</div>

  <div class="submit-button">SUBMIT</div>
  <div class="footer-social"><span class="social-dot"></span><span class="social-dot"></span><span class="social-dot"></span><span class="social-dot"></span></div>
</body>
</html>
```